Business Card Design

We like to use greens as you will see in our logo (but not TOO much green). We are a Dental Clinic in a somewhat eccentric community. We do not like the dated sharp designs which we see many dentists use. We're looking for something bright and fresh while still maintaining the integrity of the profession. Elegance is not necessarily what we are going for... we need for the design to be "mature" but also up-lifting.

See our logo.
Updates

Project Deadline Extended
Reason: We have 5 designs which we like. But we'd like to see a few more before committing to a design.

Project Deadline Extended
Reason: We are awaiting revisions to this project. We are still welcoming designs while we wait to see if designers are able to provide to us the revisions we require in order to proceed with a selection.

Target Market(s)

Younger families - ages late 20's to early 40's

Industry/Entity Type

Business

Contact Information for Business Card

Corwel T. Banfry DDS 2730 W. Halvert Rd. Ste. 7 Royal Oak, MI 48391 (248)555-0174 FX (248)555-0189 info@BrightwellDentalCareMi.com BrigthwellDentalCareMi.com on the back of the card we need an appointment reminder (For____ Date___ Time____) with "If you are unable to keep your appointment, kindly give 48 hours notice" at the bottom. No use of teeth in the design. DOUBLE SIDED DESIGN

Requirements
Should not have
• The use of pictures of teeth

```html
<!DOCTYPE html>
<html lang="en">
<head>
<meta charset="utf-8">
<title>Brightwell Dental Care – Business Card</title>
<link rel="stylesheet" href="https://fonts.googleapis.com/css2?family=Lato:wght@400;700;900&display=swap">
<style>
  :root {
    --canvas-bg: #e6e8e6;
    --card-white: #ffffff;
    --green-deep: #1f6b3a;
    --green-main: #2a8a45;
    --green-mid: #3fa34d;
    --green-light: #8cc63f;
    --ink: #1d1d1d;
    --ink-soft: #333333;
  }
  * { box-sizing: border-box; margin: 0; padding: 0; }
  html, body {
    width: 1200px; height: 926px; overflow: hidden;
    background: var(--canvas-bg);
    font-family: "Lato", Arial, sans-serif;
  }
  .canvas { position: relative; width: 1200px; height: 926px; }
  .card {
    position: absolute; left: 250px; width: 700px; height: 400px;
    overflow: hidden; box-shadow: 0 6px 18px rgba(0,0,0,.18);
  }
  .card--front { top: 42px; background: var(--card-white); }
  .card--back {
    top: 484px;
    background: radial-gradient(ellipse at 55% 30%, #3c9a55 0%, var(--green-main) 35%, var(--green-deep) 100%);
  }

  .front-band {
    position: absolute; left: 0; right: 0; top: 286px; bottom: 0;
    background: linear-gradient(90deg, var(--green-main) 0%, var(--green-mid) 60%, var(--green-light) 100%);
  }

  .brand {
    display: flex; align-items: center; gap: 8px;
    color: var(--green-main); font-weight: 700; font-size: 30px;
    letter-spacing: .3px; line-height: 1;
  }
  .brand__dot { width: 22px; height: 22px; border-radius: 50%; background: var(--green-light); }
  .card--front .brand { position: absolute; left: 46px; top: 44px; }

  .contact {
    position: absolute; left: 60px; top: 122px;
    list-style: none; font-size: 17px; color: var(--ink-soft); line-height: 25px;
  }
  .contact__key { display: inline-block; width: 24px; font-weight: 700; color: var(--ink); }

  .person { position: absolute; right: 52px; top: 118px; text-align: right; color: var(--ink); }
  .person__name { font-size: 26px; font-weight: 400; }
  .person__name strong { font-weight: 700; }
  .person__title { font-size: 15px; color: var(--green-main); margin-top: 4px; }

  .address {
    position: absolute; left: 40px; top: 340px;
    color: #ffffff; font-size: 16px; letter-spacing: .3px;
  }

  .card--back .brand {
    position: absolute; left: 0; right: 0; top: 30px; justify-content: center;
    color: #ffffff; font-size: 28px;
  }
  .appointment__title {
    position: absolute; left: 0; right: 0; top: 80px; text-align: center;
    color: #ffffff; font-size: 17px; letter-spacing: 5px; font-weight: 700;
  }
  .appointment__row {
    position: absolute; left: 150px; right: 90px; display: flex; align-items: center; gap: 16px;
  }
  .appointment__row--for { top: 118px; }
  .appointment__row--date { top: 166px; }
  .appointment__row--time { top: 214px; }
  .appointment__label {
    width: 60px; color: #ffffff; font-size: 15px; letter-spacing: 1.5px; font-weight: 700;
  }
  .appointment__field { flex: 1; height: 38px; background: #ffffff; }
  .notice {
    position: absolute; left: 0; right: 0; bottom: 0; height: 110px;
    background: rgba(10, 60, 30, .45);
    display: flex; flex-direction: column; justify-content: center; align-items: center;
    color: #ffffff; text-align: center; line-height: 1.35;
  }
  .notice__line { font-size: 20px; }
  .notice__line--strong { font-size: 22px; font-weight: 900; }
</style>
</head>
<body>
<main class="canvas">

  <section class="card card--front" aria-label="Card front">
    <div class="front-band" role="img" aria-label="Decorative green band with flowing lines and overlapping circles"></div>

    <div class="brand"><span class="brand__dot"></span>Brightwell Dental Care</div>

    <ul class="contact">
      <li><span class="contact__key">P</span>(248)555-0174</li>
      <li><span class="contact__key">F</span>(248)555-0189</li>
      <li><span class="contact__key">W</span>BrigthwellDentalCareMi.com</li>
      <li><span class="contact__key">E</span>info@BrightwellDentalCareMi.com</li>
    </ul>

    <div class="person">
      <p class="person__name">Corwel <strong>T. Banfry</strong></p>
      <p class="person__title">-DDS</p>
    </div>

    <p class="address">2730 W. Halvert Rd. Ste. 7 Royal Oak, MI 48391</p>
  </section>

  <section class="card card--back" aria-label="Card back">
    <div class="brand"><span class="brand__dot"></span>Brightwell Dental Care</div>
    <p class="appointment__title">APPOINTMENT</p>
    <div class="appointment__row appointment__row--for">
      <span class="appointment__label">FOR</span><span class="appointment__field"></span>
    </div>
    <div class="appointment__row appointment__row--date">
      <span class="appointment__label">DATE</span><span class="appointment__field"></span>
    </div>
    <div class="appointment__row appointment__row--time">
      <span class="appointment__label">TIME</span><span class="appointment__field"></span>
    </div>
    <div class="notice">
      <p class="notice__line">If you are unable to keep your appointment</p>
      <p class="notice__line notice__line--strong">kindly give 48 hours notice</p>
    </div>
  </section>

</main>
</body>
</html>
```